Business card for medical clinic

I need an upmarket, modern medical/health business card for my clinic

Contact Information for Business Card

name, address, email, qr code

```html
<!DOCTYPE html>
<html lang="en">
<head>
<meta charset="utf-8">
<title>Meridian Care Partners – Business Card</title>
<link rel="stylesheet" href="https://fonts.googleapis.com/css2?family=Cinzel:wght@500&family=PT+Serif:wght@400&display=swap">
<style>
  :root {
    --backdrop: #d1d2d4;
    --card: #ffffff;
    --brand-blue: #1c6ea4;
    --navy: #1f3553;
    --sky: #27a6e0;
    --ink: #2a2a2a;
  }
  * { margin: 0; padding: 0; box-sizing: border-box; }
  html, body { width: 900px; height: 1200px; overflow: hidden; }
  body {
    background: var(--backdrop);
    position: relative;
    font-family: "PT Serif", Georgia, serif;
    color: var(--ink);
  }
  .card {
    position: absolute;
    left: 133px;
    width: 633px;
    height: 364px;
    background: var(--card);
  }
  .card--front { top: 210px; }
  .card--back { top: 624px; }

  .brand {
    position: absolute;
    display: flex;
    align-items: center;
    gap: 14px;
    white-space: nowrap;
  }
  .brand__mark { flex: none; }
  .brand__name {
    font-family: "PT Serif", Georgia, serif;
    font-weight: 400;
    color: var(--brand-blue);
    text-transform: uppercase;
    letter-spacing: 0.06em;
  }
  .card--front .brand { left: 86px; top: 148px; }
  .card--front .brand__name { font-size: 27px; }
  .card--back .brand { left: 32px; top: 164px; }
  .card--back .brand__name { font-size: 16px; }

  .details {
    position: absolute;
    left: 316px;
    top: 94px;
    height: 178px;
    padding-left: 14px;
    border-left: 2px solid;
    border-image: linear-gradient(to bottom, var(--navy), var(--sky)) 1;
  }
  .details__name {
    font-family: "Cinzel", serif;
    font-weight: 500;
    font-size: 21px;
    line-height: 1;
    color: var(--brand-blue);
    margin-top: 4px;
  }
  .details__role { font-size: 14.5px; margin-top: 6px; }
  .details__address { font-size: 14.5px; line-height: 23px; margin-top: 12px; }
  .details__contacts { list-style: none; margin-top: 12px; font-size: 14.5px; }
  .details__contacts li {
    display: flex; align-items: center; gap: 7px; height: 25px;
  }
  .details__contacts .phone { letter-spacing: 0.18em; }
  .icon { width: 11px; height: 11px; flex: none; }
</style>
</head>
<body>
  <section class="card card--front" aria-label="Card front">
    <div class="brand">
      <svg class="brand__mark" width="40" height="40" viewBox="0 0 40 40" aria-hidden="true">
        <circle cx="20" cy="20" r="17" fill="none" stroke="#1c6ea4" stroke-width="3"/>
      </svg>
      <span class="brand__name">Meridian Care Partners</span>
    </div>
  </section>

  <section class="card card--back" aria-label="Card back">
    <div class="brand">
      <svg class="brand__mark" width="26" height="26" viewBox="0 0 26 26" aria-hidden="true">
        <circle cx="13" cy="13" r="11" fill="none" stroke="#1c6ea4" stroke-width="2"/>
      </svg>
      <span class="brand__name">Meridian Care Partners</span>
    </div>

    <div class="details">
      <h1 class="details__name">DANIEL HARPER</h1>
      <p class="details__role">Principal Consultant</p>
      <p class="details__address">PO Box 418305<br>Birch Creek, Alaska 99621</p>
      <ul class="details__contacts">
        <li>
          <svg class="icon" viewBox="0 0 24 24" aria-hidden="true"><path fill="#1c6ea4" d="M6.6 10.8a15.1 15.1 0 0 0 6.6 6.6l2.2-2.2c.3-.3.7-.4 1-.2 1.1.4 2.3.6 3.6.6.6 0 1 .4 1 1V20c0 .6-.4 1-1 1C10.6 21 3 13.4 3 4c0-.6.4-1 1-1h3.5c.6 0 1 .4 1 1 0 1.3.2 2.5.6 3.6.1.3 0 .7-.2 1z"/></svg>
          <span class="phone">+1-907-555-0142</span>
        </li>
        <li>
          <svg class="icon" viewBox="0 0 24 24" aria-hidden="true"><rect x="2" y="5" width="20" height="14" fill="#1c6ea4"/><path d="M2 5l10 8 10-8" fill="none" stroke="#fff" stroke-width="1.8"/></svg>
          <span>info@meridiancarepartners.com</span>
        </li>
        <li>
          <svg class="icon" viewBox="0 0 24 24" aria-hidden="true"><g fill="none" stroke="#1c6ea4" stroke-width="2"><circle cx="12" cy="12" r="10"/><ellipse cx="12" cy="12" rx="4" ry="10"/><path d="M2 12h20M4 7h16M4 17h16"/></g></svg>
          <span>www.meridiancarepartners.com</span>
        </li>
      </ul>
    </div>
  </section>
</body>
</html>
```